Bramblewood Card Company Business Cards

We are a trading card store with Glimmorax, sports and other TCG cards, we need a business card design that encompasses a clean cut, modern style with a retro flare. website is bramblewoodcardco.com for reference. Can utilize a comic book era feel or a more modern outdoor feel to utilize the "Pacific Northwest" elements of tress, mountains, etc.

Industry/Entity Type

Trading cards and collectibles

Contact Information for Business Card

business name, email address, phone number, name, owner job title

Font styles to use
Sans Serif

```html
<!DOCTYPE html>
<html lang="en">
<head>
<meta charset="utf-8">
<title>Bramblewood Card Company – Business Card</title>
<link rel="stylesheet" href="https://fonts.googleapis.com/css2?family=Montserrat:wght@400;500;700&display=swap">
<style>
  :root {
    --backdrop: #dcdcdb;
    --card: #1f1f21;
    --card-deep: #151516;
    --cyan: #1fbfe0;
    --white: #f4f4f4;
    --rule: #6a6a6c;
    --badge-grey: #6d6d70;
  }
  * { box-sizing: border-box; margin: 0; padding: 0; }
  html, body {
    width: 1200px; height: 801px; overflow: hidden;
    background: var(--backdrop);
    font-family: "Montserrat", sans-serif;
  }
  .stage { position: relative; width: 1200px; height: 801px; }
  .card {
    position: absolute; top: 246px;
    width: 540px; height: 309px;
    background: var(--card);
    border-bottom: 5px solid var(--cyan);
    box-shadow: 0 6px 18px rgba(0,0,0,.18);
    overflow: hidden;
  }
  .card--front { left: 40px; }
  .card--back { left: 620px; }

  .brand {
    position: absolute; top: 44px; right: 34px;
    display: flex; align-items: center; gap: 10px;
    color: var(--white); font-weight: 700; font-size: 15px;
    letter-spacing: .08em; text-transform: uppercase; line-height: 1.3;
    text-align: right;
  }
  .brand__dot { width: 14px; height: 14px; border-radius: 50%; background: var(--cyan); flex: none; }

  .person { position: absolute; left: 32px; top: 138px; }
  .person__name {
    color: var(--cyan); font-weight: 700; font-size: 27px;
    letter-spacing: .03em; text-transform: uppercase;
  }
  .person__title { color: var(--white); font-size: 16px; margin-top: 2px; }

  .divider {
    position: absolute; left: 32px; right: 28px; top: 206px;
    height: 1px; background: var(--rule);
  }

  .contact { position: absolute; left: 32px; top: 220px; list-style: none; }
  .contact li {
    display: flex; align-items: center; gap: 10px;
    color: var(--white); font-size: 15px; height: 25px;
  }
  .contact svg { width: 13px; height: 13px; fill: var(--cyan); flex: none; }
  .contact .accent { color: var(--cyan); }

  .address {
    position: absolute; right: 30px; top: 226px;
    color: var(--white); font-size: 16px; line-height: 1.5; text-align: right;
  }

  .pattern {
    position: absolute; inset: 0;
    background: linear-gradient(135deg, var(--card-deep) 0%, #232325 45%, #4a4a4d 100%);
  }
  .back-brand {
    position: absolute; right: 60px; bottom: 70px;
    padding: 8px 12px; background: var(--card);
    color: var(--cyan); font-weight: 700; font-size: 12px;
    letter-spacing: .08em; text-transform: uppercase;
  }
</style>
</head>
<body>
<main class="stage">
  <section class="card card--front" aria-label="Business card front">
    <div class="brand">
      <span class="brand__dot"></span>
      <span>Bramblewood<br>Card Company</span>
    </div>

    <div class="person">
      <p class="person__name">Dorian Pell</p>
      <p class="person__title">CEO/Founder</p>
    </div>

    <div class="divider"></div>

    <ul class="contact">
      <li>
        <svg viewBox="0 0 24 24" aria-hidden="true"><path d="M6.6 10.8a15.1 15.1 0 0 0 6.6 6.6l2.2-2.2c.3-.3.7-.4 1-.2 1.1.4 2.3.6 3.6.6.6 0 1 .4 1 1V20c0 .6-.4 1-1 1A17 17 0 0 1 3 4c0-.6.4-1 1-1h3.5c.6 0 1 .4 1 1 0 1.3.2 2.5.6 3.6.1.3 0 .7-.2 1z"/></svg>
        (555) 204 7716
      </li>
      <li>
        <svg viewBox="0 0 24 24" aria-hidden="true"><path d="M2 5h20v14H2z M2 5l10 8 10-8" /></svg>
        info@bramblewoodcardco.com
      </li>
      <li>
        <svg viewBox="0 0 24 24" aria-hidden="true"><path d="M12 2a10 10 0 1 0 0 20 10 10 0 0 0 0-20zm6.9 6h-3a15 15 0 0 0-1.3-4A8 8 0 0 1 18.9 8zM12 4c.8 1.2 1.5 2.5 1.9 4h-3.8c.4-1.5 1.1-2.8 1.9-4zM4.3 14a8 8 0 0 1 0-4h3.4a16 16 0 0 0 0 4zm.8 2h3a15 15 0 0 0 1.3 4A8 8 0 0 1 5.1 16zm3-8h-3a8 8 0 0 1 4.3-4c-.6 1.2-1 2.6-1.3 4zM12 20c-.8-1.2-1.5-2.5-1.9-4h3.8c-.4 1.5-1.1 2.8-1.9 4zm2.3-6H9.7a14 14 0 0 1 0-4h4.6a14 14 0 0 1 0 4zm.3 6c.6-1.2 1-2.6 1.3-4h3a8 8 0 0 1-4.3 4zm1.7-6a16 16 0 0 0 0-4h3.4a8 8 0 0 1 0 4z"/></svg>
        <span>www.<span class="accent">bramblewoodcardco</span>.com</span>
      </li>
    </ul>

    <p class="address">P.O. Box 3318 Lane<br>Region Name CD 6120</p>
  </section>

  <section class="card card--back" aria-label="Business card back">
    <div class="pattern" role="img" aria-label="Repeating pattern of company badges in shades of grey fading to black"></div>
    <p class="back-brand">Bramblewood Card Company</p>
  </section>
</main>
</body>
</html>
```